Website Design for a Luxury Wedding & Events Company

We are launching a British luxury wedding & event planning consultancy business providing bespoke, elegant and first-class service to our discerning clients in the UK and abroad. We specialize in Weddings (which will have it's on page) however we also provide service for other occasion which will be included in a single page 'Events'.

We require a company website design befitting of our luxury brand. Once designed we will post another job to code the website so that it can be hosted by HostPlume.com.

The website has to set the tone for our business and type of premium service we provide. Our website design has to be BESPOKE and have a luxury and elegant look and feel about it.

PLEASE REFER TO THE IMAGES ATTACHED TO GET AN UNDERSTANDING OF THE DESIGN CONCEPT WE WANT. ALL DESIGNS SUBMITTED MUST FOLLOW THE CONCEPT SPECIFIED!!!

We appreciate that the current budget will not permit for the design of all pages referenced above, so we are happy to have designs for up to 3 pages initially; Landing page (we have attached an examples of what we want), 'Home' page (an example is also attached) and 'About' us page. When we are happy with a particular design we can add payment for remainder of the pages required.

The final website design will have the following pages:
1a) URL Landing Page (details below)
1b) Home
2) About
3) Luxury Weddings
4) Services (this can either be a separate tab or linked to 'Luxury Weddings' - however it does need to be a separate page)
subheadings are:
> Comprehensive Wedding Planning Service
> Wedding Day Coordination Service
> Consultancy Service
5) Events
6) Gallery
7) Testimonials
8) Contact

We have a concept of the website is as follows:
URL Landing Page:
Option 1: This should just be simple but makes an immediate statement.
We have attached an image of how this could potentially look. The logo featured in the photo example needs to be replaced with our logo (reference site: http://tesslovank.com/).

Option 2: Alternatively this could be an actually door in the middle of the page - Imagine the big black gloss door at Number 14 Corwell Terrace (London Prime Minister's home).

By clicking the door knocker on either options , the 'Home Page' will be opened.

Our tag line should also be tastefully integrated:
'Exclusive Events, Masterfully Produced, Distinctively Designed'

The 'HOME PAGE' - should look like a luxury boutique office or reception lounge (luxury table, luxury head chair and luxury 2 client chairs; elegant chandelier, beautiful flowers on the table, 2 flutes of champagne on the table; and filing cabinets with drawers that are labelled with different website pages, e.g. 'about us', 'services', 'gallery', etc. By clicking on the drawers the details behind that page will open up in a separate tab/page.)

Our tag line should be on the Home Page also.

The overall concept and look and feel of website is all about taking people on a journey and giving them a glimpse of the luxury service that awaits them.

Colours: We want the general look and feel of the website to be WHITE, or OFF-WHITE with soft hints of gold to match the logo (tab/page headings could be gold). The only dark page should be the URL Landing page (ref to website images attached).

The website and images need to be compatible with mobile devices, smartphones, Tabros, etc. In terms of fit to screen, resolution etc...

We require links to our Pagewall, Quillet, Snapvuely and Boardlyne Pages (links to be provided later)

This is the rough concept and looking for designers to try to elevate this vision. :-) We are open for designers to interpret this concept in their own way.

Website wording/content is all ready to go...

We have attached our logo, and some imagery to help...

Target Market(s)

Luxury Wedding & Events Market

Industry/Entity Type

Wedding Planner

Number of Pages Required

3 page

Font styles to use
Sans Serif

Colors
ffffff

Requirements
Must have
• Tag Line:
• 'Exquisite Events, Masterfully Produced, Distinctively Designed'

```html
<!DOCTYPE html>
<html lang="en">
<head>
<meta charset="utf-8">
<title>Elswick Rowe — Luxury Wedding &amp; Event Planning</title>
<link rel="stylesheet" href="https://fonts.googleapis.com/css2?family=PT+Serif&family=Raleway:wght@400;500;600&family=Open+Sans:ital,wght@0,400;0,600;1,400&display=swap">
<style>
:root{
  --black:#000;
  --gold:#d6a14a;
  --gold-text:#d9a34b;
  --ribbon:#e2b866;
  --ribbon-dark:#c89540;
  --ink:#2b2b2b;
  --body:#555;
  --line:#dedede;
  --cream:#f8e9cc;
  --white:#fff;
}
*{margin:0;padding:0;box-sizing:border-box}
html,body{width:699px;height:1200px;overflow:hidden;background:var(--white)}
body{position:relative;font-family:"Open Sans",sans-serif;color:var(--ink)}
h1,h2,h3{font-weight:400}
.abs{position:absolute}
.site-header{left:0;top:0;width:699px;height:110px;background:var(--black)}
.brand-name{left:0;top:38px;width:699px;text-align:center;font-family:"Raleway",sans-serif;font-weight:500;font-size:20px;color:var(--white)}
.nav-ribbon{left:95px;top:88px;z-index:2}
.main-nav{left:117px;top:88px;width:461px;height:28px;display:flex;justify-content:space-around;align-items:center;padding:0 8px;font-family:"Raleway",sans-serif;font-size:8px;font-weight:500;color:var(--white);z-index:3}
.hero{left:0;top:110px;width:699px;height:320px;background:linear-gradient(170deg,#f3f2f6 0%,#fff 30%,#ecebf0 55%,#fff 80%)}
.hero-title{left:125px;top:170px;font-family:"PT Serif",serif;font-size:26px;color:var(--ink)}
.hero-sub{left:125px;font-family:"PT Serif",serif;font-size:16px;color:var(--gold-text)}
.btn-more{left:126px;top:258px;width:64px;height:21px;border:1.5px solid #333;border-radius:2px;font-family:"Raleway",sans-serif;font-size:8px;font-weight:500;display:flex;align-items:center;justify-content:center}
.hero-photo{left:355px;top:142px;width:216px;height:160px;border-radius:26px;border:5px solid #e4e3e6;background:linear-gradient(135deg,#c9c4c4,#efecea 50%,#a9a2a0)}
.arrow{top:205px}
.about-title{left:0;top:374px;width:699px;text-align:center;font-family:"PT Serif",serif;font-size:19px}
.about-text{left:135px;width:430px;text-align:center;font-size:5.6px;line-height:8.6px;color:var(--body)}
.services{left:0;top:504px;width:699px;height:200px;background:linear-gradient(#f0d592,#d9a74e)}
.services-title{left:0;top:22px;width:699px;text-align:center;font-family:"PT Serif",serif;font-size:16px;color:var(--ink)}
.service{top:58px;width:140px;text-align:center;font-family:"Raleway",sans-serif;font-size:9.5px;line-height:14.5px;color:var(--white)}
.service svg{display:block;margin:0 auto 18px}
.divider{top:60px;width:1px;height:110px;background:rgba(255,255,255,.35)}
.section-title{font-family:"PT Serif",serif;font-size:15px}
.events-title{left:0;top:732px;width:699px;text-align:center}
.card{top:767px;width:148px;height:139px;border:1px solid var(--line);background:var(--white)}
.card-photo{height:68px}
.card h3{margin:13px 0 0 8px;font-family:"Raleway",sans-serif;font-size:10px;color:var(--gold-text)}
.card p{margin:3px 8px 0;font-size:5.3px;line-height:9px;color:var(--body)}
.card .more{display:block;margin:6px 0 0 9px;font-size:5.8px;font-weight:600;color:var(--ink)}
.gallery-title{left:120px;top:941px}
.tile{background:linear-gradient(135deg,#ddd,#fff 50%,#777)}
.testimonials-title{left:370px;top:941px;color:var(--gold-text)}
.avatar{width:48px;height:48px;border-radius:50%;background:linear-gradient(135deg,#f1c9a8,#b8754d)}
.quote{left:430px;width:150px;font-size:5.8px;line-height:9.4px;font-style:italic;color:#888}
.quote b{font-style:normal;color:#999;font-size:12px;font-family:"PT Serif",serif;margin-right:2px}
.author{left:430px;font-size:6px;font-weight:600;color:#555}
.site-footer{left:0;top:1135px;width:699px;height:65px;background:var(--cream)}
.footer-nav{left:124px;top:21px;font-family:"PT Serif",serif;font-size:7.2px;color:var(--ink)}
.copyright{left:124px;top:38px;font-size:5.6px;color:#444}
.social{left:500px;top:22px;display:flex;gap:5px;font-family:"Open Sans",sans-serif;font-size:5.6px;font-weight:600;color:#444}
</style>
</head>
<body>
<header class="abs site-header">
  <div class="abs brand-name">Elswick Rowe</div>
</header>

<svg class="abs nav-ribbon" width="510" height="42" viewBox="0 0 510 42">
  <path d="M0 30 L30 20 L30 38 Q14 42 0 30Z" fill="#c89540"/>
  <path d="M510 30 L480 20 L480 38 Q496 42 510 30Z" fill="#c89540"/>
  <rect x="22" y="0" width="466" height="28" fill="#e2b866"/>
</svg>
<nav class="abs main-nav">
  <span>HOME</span><span>ABOUT</span><span>LUXURY WEDDINGS</span><span>SERVICES</span><span>EVENTS</span><span>GALLERY</span><span>TESTIMONIALS</span><span>CONTACT</span>
</nav>

<section class="abs hero"></section>
<h1 class="abs hero-title">Exclusive Events,</h1>
<p class="abs hero-sub" style="top:204px">Masterfully Produced,</p>
<p class="abs hero-sub" style="top:228px">Distinctively Designed</p>
<div class="abs btn-more">Read More</div>
<div class="abs hero-photo" role="img" aria-label="Bride reclining on an ornate sofa in a framed portrait"></div>
<svg class="abs arrow" style="left:76px" width="14" height="34"><path d="M13 1 L1 17 L13 33" fill="none" stroke="#666" stroke-width="1"/></svg>
<svg class="abs arrow" style="left:602px" width="14" height="34"><path d="M1 1 L13 17 L1 33" fill="none" stroke="#666" stroke-width="1"/></svg>

<h2 class="abs about-title">ABOUT ELSWICK ROWE</h2>
<p class="abs about-text" style="top:407px">Elswick Rowe is a British luxury wedding and event planning consultancy providing bespoke, elegant and first-class service to our discerning clients in the UK and abroad. Our specialist team of event planning consultants will help elevate your vision and create impeccable designs for life's most important occasions with refinement and tasteful restraint. For us merely satisfying expectations is not enough, we aim to always surpass them.</p>
<p class="abs about-text" style="top:438px">We possess an extraordinary commitment to excellence and attention to detail. Whether you are planning a grand or intimate event, we will listen to your requirements and work with you to create a completely personalised and unforgettable occasion.</p>

<section class="abs services">
  <h2 class="abs services-title">OUR SERVICES</h2>
  <div class="abs divider" style="left:286px"></div>
  <div class="abs divider" style="left:427px"></div>
  <div class="abs service" style="left:138px">
    <svg width="60" height="60" viewBox="0 0 60 60"><circle cx="30" cy="30" r="28" fill="none" stroke="#fff" stroke-width="1"/><circle cx="30" cy="30" r="22" fill="none" stroke="#fff" stroke-width="1.5"/><rect x="20" y="21" width="20" height="18" rx="2" fill="none" stroke="#fff" stroke-width="2"/><line x1="20" y1="26" x2="40" y2="26" stroke="#fff" stroke-width="2"/><line x1="25" y1="18" x2="25" y2="23" stroke="#fff" stroke-width="2"/><line x1="35" y1="18" x2="35" y2="23" stroke="#fff" stroke-width="2"/></svg>
    Comprehensive Wedding<br>Planning Service
  </div>
  <div class="abs service" style="left:285px">
    <svg width="60" height="60" viewBox="0 0 60 60"><circle cx="30" cy="30" r="28" fill="none" stroke="#fff" stroke-width="1"/><circle cx="30" cy="30" r="22" fill="none" stroke="#fff" stroke-width="1.5"/><circle cx="26" cy="29" r="6" fill="none" stroke="#fff" stroke-width="2.2"/><circle cx="34" cy="33" r="6" fill="none" stroke="#fff" stroke-width="2.2"/></svg>
    Wedding Day<br>Coordination Service
  </div>
  <div class="abs service" style="left:426px">
    <svg width="60" height="60" viewBox="0 0 60 60"><circle cx="30" cy="30" r="28" fill="none" stroke="#fff" stroke-width="1"/><circle cx="30" cy="30" r="22" fill="none" stroke="#fff" stroke-width="1.5"/><ellipse cx="27" cy="27" rx="8" ry="5.5" fill="none" stroke="#fff" stroke-width="2"/><path d="M33 31 Q40 31 39 37" fill="none" stroke="#fff" stroke-width="2"/></svg>
    Consultancy<br>Service
  </div>
</section>

<h2 class="abs section-title events-title">Other Special Events</h2>
<article class="abs card" style="left:125px">
  <div class="card-photo" role="img" aria-label="Outdoor wedding reception tables on a lawn" style="background:linear-gradient(#9fb3a0,#e9ece6 60%,#7b8a5e)"></div>
  <h3>Wedding Event here</h3>
  <p>Libero interdum nec interdum vel blandit sed nulla in ullamcorper est eget tempor cursus neq</p>
  <span class="more">READ MORE</span>
</article>
<article class="abs card" style="left:280px">
  <div class="card-photo" role="img" aria-label="Banquet hall set for a wedding dinner" style="background:linear-gradient(#a86f55,#e7ddd5 60%,#c9b7a8)"></div>
  <h3>Wedding Event here</h3>
  <p>Libero interdum nec interdum vel blandit sed nulla in ullamcorper est eget tempor cursus neq</p>
  <span class="more">READ MORE</span>
</article>
<article class="abs card" style="left:435px">
  <div class="card-photo" role="img" aria-label="Bridal party in white dresses" style="background:linear-gradient(135deg,#d8b48a,#f5f1ec 50%,#8d6c58)"></div>
  <h3>Wedding Event here</h3>
  <p>Libero interdum nec interdum vel blandit sed nulla in ullamcorper est eget tempor cursus neq</p>
  <span class="more">READ MORE</span>
</article>

<h2 class="abs section-title gallery-title">Our Gallery</h2>
<div class="abs tile" style="left:120px;top:970px;width:100px;height:62px" role="img" aria-label="Reception tables with black and white linen"></div>
<div class="abs tile" style="left:222px;top:970px;width:127px;height:62px;background:linear-gradient(135deg,#e9c79a,#fff 50%,#b33a2e)" role="img" aria-label="Table runner with red roses"></div>
<div class="abs tile" style="left:120px;top:1035px;width:75px;height:47px;background:linear-gradient(135deg,#c7b3e0,#fff 50%,#7a3fa8)" role="img" aria-label="Wedding cake with purple ribbon"></div>
<div class="abs tile" style="left:198px;top:1035px;width:75px;height:47px;background:linear-gradient(135deg,#e8e8e8,#fff 50%,#aaa)" role="img" aria-label="White table settings with floral centrepieces"></div>
<div class="abs tile" style="left:275px;top:1035px;width:74px;height:47px;background:linear-gradient(135deg,#c3477a,#f2d0e0 50%,#7a2348)" role="img" aria-label="Ballroom lit in pink and purple"></div>

<h2 class="abs section-title testimonials-title">Testimonials</h2>
<div class="abs avatar" style="left:374px;top:970px" role="img" aria-label="Portrait of a happy couple"></div>
<p class="abs quote" style="top:970px"><b>&ldquo;</b>Donec dictum lectus non odio Cras a ante vitae enim iaculis aliquam Mauris nunc quam venenatis nec euismod sit amet egestas placerat est Pellentesque habitant morbi tristique senectus</p>
<div class="abs author" style="top:1012px">By Author Name</div>
<div class="abs avatar" style="left:374px;top:1034px" role="img" aria-label="Portrait of a smiling couple"></div>
<p class="abs quote" style="top:1036px"><b>&ldquo;</b>Mauris vel lacus vitae felis vestibulum volutpat Etiam est nunc venenatis in tristique eu imperdiet ac nisl Cum sociis natoque penatibus et magnis</p>
<div class="abs author" style="top:1068px">By Author Name</div>

<footer class="abs site-footer">
  <nav class="abs footer-nav">HOME &nbsp;|&nbsp; ABOUT &nbsp;|&nbsp; LUXURY WEDDINGS &nbsp;|&nbsp; SERVICES &nbsp;|&nbsp; EVENTS &nbsp;|&nbsp; GALLERY &nbsp;|&nbsp; TESTIMONIALS &nbsp;|&nbsp; CONTACT</nav>
  <p class="abs copyright">© 2015 Company Name &nbsp;All right reserved &nbsp;Term of Use</p>
  <div class="abs social"><span>Pagewall</span><span>Quillet</span><span>Boardlyne</span><span>Snapvuely</span></div>
</footer>
</body>
</html>
```